Book Cover with this title and sub title
Where Auntie Found Her Quiet Orchard
The little book to be smart with your money and help the environment.
Walter P. Brunk Ph. D.
Ellen R. Brunk
Picture below would be on the entire front cover. Words somehow incorporated for easy reading.

```html
<!DOCTYPE html>
<html lang="en">
<head>
<meta charset="utf-8">
<title>Where Auntie Found Her Quiet Orchard — Book Cover</title>
<link rel="stylesheet" href="https://fonts.googleapis.com/css2?family=Bebas+Neue&family=Cinzel:wght@400;500&display=swap">
<style>
  :root {
    --sky: #0797ea;
    --sky-light: #1aa3ee;
    --bloom: #f2c318;
    --bloom-deep: #b8870f;
    --title-white: #ffffff;
    --title-gold: #f5bf0c;
    --shadow: rgba(0, 40, 90, 0.55);
  }
  html, body {
    margin: 0;
    padding: 0;
    width: 934px;
    height: 1200px;
    overflow: hidden;
    background: var(--sky);
  }
  .cover {
    position: relative;
    width: 934px;
    height: 1200px;
    overflow: hidden;
  }
  .cover-photo {
    position: absolute;
    inset: 0;
    background: linear-gradient(180deg,
      var(--sky) 0%,
      var(--sky-light) 52%,
      #3aa6c8 68%,
      var(--bloom) 82%,
      var(--bloom-deep) 100%);
  }
  .title-block {
    position: absolute;
    left: 0;
    right: 0;
    top: 168px;
    text-align: center;
  }
  .title-lead {
    margin: 0;
    font-family: 'Bebas Neue', 'Oswald', sans-serif;
    font-size: 100px;
    line-height: 1;
    color: var(--title-white);
    letter-spacing: 0.5px;
    text-shadow: 3px 5px 8px var(--shadow);
  }
  .title-link {
    margin: 18px 0 0;
    font-family: 'Cinzel', serif;
    font-size: 30px;
    line-height: 1;
    letter-spacing: 11px;
    color: var(--title-white);
  }
  .title-main {
    margin: 10px 0 0;
    font-family: 'Cinzel', serif;
    font-weight: 400;
    font-size: 122px;
    line-height: 1;
    letter-spacing: 4px;
    color: var(--title-gold);
    text-shadow: 4px 6px 8px var(--shadow);
  }
  .subtitle {
    position: absolute;
    top: 438px;
    left: 0;
    right: 0;
    text-align: center;
    font-family: 'Bebas Neue', 'Oswald', sans-serif;
    font-size: 40px;
    line-height: 46px;
    color: var(--title-white);
    text-shadow: 3px 4px 6px var(--shadow);
    margin: 0;
  }
  .subtitle-rule {
    position: absolute;
    top: 478px;
    width: 95px;
    height: 3px;
    background: var(--title-white);
  }
  .subtitle-rule.left { left: 123px; }
  .subtitle-rule.right { left: 728px; }
  .authors {
    position: absolute;
    top: 1030px;
    left: 0;
    right: 0;
    text-align: center;
    font-family: 'Cinzel', serif;
    font-size: 60px;
    line-height: 62px;
    color: var(--title-white);
    text-shadow: 2px 3px 6px rgba(80, 50, 0, 0.45);
  }
  .author { margin: 0; }
</style>
</head>
<body>
  <main class="cover">
    <div class="cover-photo" role="img" aria-label="Honeybee gathering pollen on a yellow flower against a clear blue sky"></div>

    <header class="title-block">
      <h1 class="title-lead">Where Auntie Found</h1>
      <p class="title-link">HER QUIET</p>
      <p class="title-main">ORCHARD</p>
    </header>

    <span class="subtitle-rule left"></span>
    <p class="subtitle">THE LITTLE BOOK TO BE SMART WITH YOUR<br>MONEY AND HELP THE ENVIRONMENT.</p>
    <span class="subtitle-rule right"></span>

    <footer class="authors">
      <p class="author">Walter P. Brunk Ph. D.</p>
      <p class="author">Ellen R. Brunk</p>
    </footer>
  </main>
</body>
</html>
```